Maplecrest Disability - Social Security Disability Attorneys

Our company is expanding to attract clients nationwide for our social security disability practice. We have a logo, but I am looking for a creative and elegant letterhead that projects an image of being technologically advanced but still professional enough for the legal field. I am looking for the "wow factor" combined with this is still professional enough for a law practice.

Requesting letterhead and business card design
Updates

Had to update and change the logo. The previous logo had a typo. Please send updates with the new logo for consideration. The letterhead and business cards should be professional enough to be used for a law firm. Thanks.

Industry/Entity Type

Law Practice, Law Firm, Healthcare Industry, Government

Colors

Designer to choose colors to be used in the design.

Requirements
Nice to have
• **Please create a vertical design for the business card**

```html
<!DOCTYPE html>
<html lang="en">
<head>
<meta charset="UTF-8">
<title>Maplecrest Disability – Business Card</title>
<link href="https://fonts.googleapis.com/css2?family=Montserrat:wght@400;500;700&display=swap" rel="stylesheet">
<style>
  :root {
    --backdrop: #2b2b2b;
    --card: #171717;
    --brand-blue: #4d66b3;
    --accent-orange: #f07c22;
    --ink-light: #f2f2f2;
  }
  * { box-sizing: border-box; margin: 0; padding: 0; }
  html, body { width: 1200px; height: 1200px; overflow: hidden; }
  body {
    background: var(--backdrop);
    font-family: "Montserrat", sans-serif;
    position: relative;
  }
  .card {
    position: absolute;
    top: 240px;
    width: 420px;
    height: 720px;
    background: var(--card);
    border-radius: 28px;
    color: var(--ink-light);
  }
  .card--front { left: 150px; }
  .card--back { left: 630px; }

  /* Front */
  .brand {
    position: absolute;
    top: 110px;
    left: 0; right: 0;
    display: flex;
    align-items: center;
    justify-content: center;
    gap: 12px;
  }
  .brand__dot {
    width: 16px; height: 16px;
    border-radius: 50%;
    background: var(--accent-orange);
  }
  .brand__name {
    color: var(--brand-blue);
    font-weight: 500;
    font-size: 24px;
    letter-spacing: 1px;
    text-transform: uppercase;
  }
  .person {
    position: absolute;
    top: 220px;
    left: 0; right: 0;
    text-align: center;
  }
  .person__name {
    color: var(--accent-orange);
    font-weight: 700;
    font-size: 27px;
    text-transform: uppercase;
  }
  .person__role {
    display: flex;
    align-items: center;
    justify-content: center;
    gap: 8px;
    margin-top: 6px;
    font-size: 19px;
  }
  .person__rule {
    width: 70px; height: 2px;
    background: var(--accent-orange);
  }
  .address {
    position: absolute;
    top: 345px;
    left: 0; right: 0;
    text-align: center;
    font-size: 17px;
    line-height: 1.45;
  }
  .contact-icons {
    position: absolute;
    top: 450px;
    left: 0; right: 0;
    display: flex;
    justify-content: center;
    gap: 38px;
  }
  .contact-icons svg { width: 22px; height: 22px; fill: var(--accent-orange); }
  .contact-rule {
    position: absolute;
    top: 492px;
    left: 110px; right: 110px;
    height: 2px;
    background: var(--accent-orange);
  }
  .contact-list {
    position: absolute;
    top: 510px;
    left: 0; right: 0;
    list-style: none;
    text-align: center;
    font-size: 16px;
    line-height: 1.65;
  }

  /* Back */
  .back-brand {
    position: absolute;
    top: 50%; left: 50%;
    transform: translate(-50%, -50%) rotate(-90deg);
    display: flex;
    align-items: center;
    gap: 20px;
    white-space: nowrap;
  }
  .back-brand__dot {
    width: 40px; height: 40px;
    border-radius: 50%;
    background: var(--accent-orange);
  }
  .back-brand__name {
    color: var(--ink-light);
    font-weight: 500;
    font-size: 38px;
    letter-spacing: 2px;
    text-transform: uppercase;
  }
</style>
</head>
<body>
  <section class="card card--front">
    <div class="brand">
      <span class="brand__dot"></span>
      <span class="brand__name">Maplecrest Disability</span>
    </div>

    <div class="person">
      <p class="person__name">Dana Whitcombe</p>
      <p class="person__role"><span class="person__rule"></span>Co-Founder<span class="person__rule"></span></p>
    </div>

    <p class="address">Suite 4, Level 12, Harbour Lane<br>Ashford NSW 2100</p>

    <div class="contact-icons">
      <svg viewBox="0 0 24 24" aria-label="Phone"><path d="M6.6 10.8a15.1 15.1 0 0 0 6.6 6.6l2.2-2.2a1 1 0 0 1 1-.25 11.4 11.4 0 0 0 3.6.57 1 1 0 0 1 1 1V20a1 1 0 0 1-1 1A17 17 0 0 1 3 4a1 1 0 0 1 1-1h3.5a1 1 0 0 1 1 1c0 1.25.2 2.45.57 3.57a1 1 0 0 1-.25 1z"/></svg>
      <svg viewBox="0 0 24 24" aria-label="Email"><path d="M2 5h20v14H2z" opacity="0"/><path d="M3 5h18a1 1 0 0 1 1 1v12a1 1 0 0 1-1 1H3a1 1 0 0 1-1-1V6a1 1 0 0 1 1-1zm1 2v.4l8 5.2 8-5.2V7z"/></svg>
      <svg viewBox="0 0 24 24" aria-label="Website"><path d="M12 2a10 10 0 1 0 0 20 10 10 0 0 0 0-20zm6.9 6h-2.9a15.6 15.6 0 0 0-1.4-3.6A8 8 0 0 1 18.9 8zM12 4c.8 1.2 1.5 2.5 1.9 4h-3.8c.4-1.5 1.1-2.8 1.9-4zM4.3 14a8 8 0 0 1 0-4h3.4a16 16 0 0 0 0 4zm.8 2h2.9a15.6 15.6 0 0 0 1.4 3.6A8 8 0 0 1 5.1 16zM8 8H5.1a8 8 0 0 1 4.3-3.6C8.8 5.5 8.4 6.7 8 8zm4 12c-.8-1.2-1.5-2.5-1.9-4h3.8c-.4 1.5-1.1 2.8-1.9 4zm2.3-6H9.7a14.7 14.7 0 0 1 0-4h4.6a14.7 14.7 0 0 1 0 4zm.3 5.6c.6-1.1 1.1-2.3 1.4-3.6h2.9a8 8 0 0 1-4.3 3.6zm1.7-5.6a16 16 0 0 0 0-4h3.4a8 8 0 0 1 0 4z"/></svg>
    </div>
    <div class="contact-rule"></div>

    <ul class="contact-list">
      <li>555-014-2290</li>
      <li>info@maplecrestdisability.com</li>
      <li>www.maplecrestdisability.com</li>
    </ul>
  </section>

  <section class="card card--back">
    <div class="back-brand">
      <span class="back-brand__dot"></span>
      <span class="back-brand__name">Maplecrest Disability</span>
    </div>
  </section>
</body>
</html>
```